New National Dermatology Group needs a business card!

We need a business card for our new national company that has 3 brands within the business:
Lumora Clinics Australia, Tessaly Clinics Australia and Corvane Clinics Australia.
We help people access dermatology services close to home throughout Australia.
We need a business card that has:
all 3 logos on it,
Our websites (there are three, listed above)
Our email (there are three, listed above)
The location of our first clinic: 41 Willow Rd Parramatta (this can then be changed for each location as required)

```html
<!DOCTYPE html>
<html lang="en">
<head>
<meta charset="utf-8">
<title>National Dermatology Group — Business Card</title>
<link href="https://fonts.googleapis.com/css2?family=Arimo:wght@400;700&display=swap" rel="stylesheet">
<style>
  :root{
    --bg:#2d2d2f;
    --white:#ffffff;
    --brown:#7a3f1c;
    --green:#1fa94a;
    --orange:#ee8427;
    --ink:#1e1e1e;
  }
  *{box-sizing:border-box;margin:0;padding:0}
  html,body{width:1200px;height:866px;overflow:hidden;background:var(--bg)}
  .stage{position:relative;width:1200px;height:866px}
  .card{position:absolute;top:278px;width:540px;height:309px;overflow:hidden;
        box-shadow:0 10px 24px rgba(0,0,0,.45)}
  .card--front{left:40px;background:var(--white)}
  .card--back{left:620px;
    background:linear-gradient(200deg,var(--orange) 0%,var(--green) 38%,#22a84a 55%,#6f4a1d 88%,#7a3f1c 100%)}

  /* contact list */
  .contacts{position:absolute;left:30px;top:24px;font-family:Arimo,sans-serif;font-size:12.5px;color:var(--ink)}
  .contact-group{margin-bottom:6px}
  .contact-line{display:flex;align-items:center;gap:7px;line-height:17px;white-space:nowrap}
  .contact-line svg{width:12px;height:12px;flex:none}
  .group--brown{--accent:var(--brown)}
  .group--green{--accent:var(--green)}
  .group--orange{--accent:var(--orange)}
  .contact-group svg{fill:var(--accent)}
  .accent{color:var(--accent)}

  /* brand names: plain text wordmarks, one colour and weight each */
  .brands{position:absolute;font-family:Arimo,sans-serif;font-weight:700;text-transform:uppercase}
  .brands--front{right:30px;top:104px;text-align:right}
  .brand{margin-bottom:9px}
  .brand-name{display:block;font-size:27px;line-height:29px;letter-spacing:1px}
  .brand-sub{display:block;font-size:8.5px;line-height:11px;letter-spacing:3px}
  .brand--corvane{color:var(--brown)}
  .brand--lumora{color:var(--green)}
  .brand--tessaly{color:var(--orange)}

  .brands--back{left:0;right:0;top:62px;text-align:center;color:var(--white)}
  .brands--back .brand{margin-bottom:12px}
  .brands--back .brand-name{font-size:36px;line-height:40px;letter-spacing:2px}
  .brands--back .brand-sub{font-size:10px;line-height:13px;letter-spacing:4.4px}

  .footer-band{position:absolute;left:0;bottom:0;width:540px;height:90px}
</style>
</head>
<body>
<svg width="0" height="0" style="position:absolute" aria-hidden="true">
  <defs>
    <symbol id="icon-mail" viewBox="0 0 24 24"><path d="M2 5h20v14H2z"/><path d="M2 5l10 8 10-8v2l-10 8L2 7z" fill="#fff"/></symbol>
    <symbol id="icon-web" viewBox="0 0 24 24"><path fill-rule="evenodd" d="M12 1a11 11 0 1 1 0 22 11 11 0 0 1 0-22zm-1 3a14 8 0 0 0-3 7h3zm2 0v7h3a14 8 0 0 0-3-7zM3.2 11h2.9a16 9 0 0 1 1.6-6 9 9 0 0 0-4.5 6zm14.7 0h2.9a9 9 0 0 0-4.5-6 16 9 0 0 1 1.6 6zM3.2 13a9 9 0 0 0 4.5 6 16 9 0 0 1-1.6-6zm4.8 0a14 8 0 0 0 3 7v-7zm5 0v7a14 8 0 0 0 3-7zm4.9 0a16 9 0 0 1-1.6 6 9 9 0 0 0 4.5-6z"/></symbol>
    <symbol id="icon-pin" viewBox="0 0 24 24"><path fill-rule="evenodd" d="M12 1a8 8 0 0 1 8 8c0 6-8 14-8 14S4 15 4 9a8 8 0 0 1 8-8zm0 5a3 3 0 1 0 0 6 3 3 0 0 0 0-6z"/></symbol>
  </defs>
</svg>

<main class="stage">
  <section class="card card--front" aria-label="Card front">
    <div class="contacts">
      <div class="contact-group group--brown">
        <p class="contact-line"><svg><use href="#icon-mail"/></svg><span>info@clinicmail.com.au</span></p>
        <p class="contact-line"><svg><use href="#icon-web"/></svg><span>www.<span class="accent">clinicsite</span>.com.au</span></p>
        <p class="contact-line"><svg><use href="#icon-pin"/></svg><span>41 Willow Rd Parramatta</span></p>
      </div>
      <div class="contact-group group--green">
        <p class="contact-line"><svg><use href="#icon-mail"/></svg><span>info@clinicmail.com.au</span></p>
        <p class="contact-line"><svg><use href="#icon-web"/></svg><span>www.<span class="accent">clinicsite</span>.com.au</span></p>
        <p class="contact-line"><svg><use href="#icon-pin"/></svg><span>41 Willow Rd Parramatta</span></p>
      </div>
      <div class="contact-group group--orange">
        <p class="contact-line"><svg><use href="#icon-mail"/></svg><span>info@clinicmail.com.au</span></p>
        <p class="contact-line"><svg><use href="#icon-web"/></svg><span>www.<span class="accent">clinicsite</span>.com.au</span></p>
        <p class="contact-line"><svg><use href="#icon-pin"/></svg><span>41 Willow Rd Parramatta</span></p>
      </div>
    </div>

    <div class="brands brands--front">
      <div class="brand brand--corvane"><span class="brand-name">Corvane</span><span class="brand-sub">Clinics Australia</span></div>
      <div class="brand brand--lumora"><span class="brand-name">Lumora</span><span class="brand-sub">Clinics Australia</span></div>
      <div class="brand brand--tessaly"><span class="brand-name">Tessaly</span><span class="brand-sub">Clinics Australia</span></div>
    </div>

    <svg class="footer-band" viewBox="0 0 540 90" aria-hidden="true">
      <path d="M0 32 L250 32" stroke="var(--orange)" stroke-width="5"/>
      <path d="M0 43 L240 43" stroke="var(--green)" stroke-width="5"/>
      <path d="M0 54 L232 54" stroke="var(--orange)" stroke-width="4"/>
      <path d="M0 62 L225 62 C250 62 250 42 285 42 L540 42 L540 90 L0 90 Z" fill="var(--brown)"/>
    </svg>
  </section>

  <section class="card card--back" aria-label="Card back">
    <div class="brands brands--back">
      <div class="brand"><span class="brand-name">Corvane</span><span class="brand-sub">Clinics Australia</span></div>
      <div class="brand"><span class="brand-name">Lumora</span><span class="brand-sub">Clinics Australia</span></div>
      <div class="brand"><span class="brand-name">Tessaly</span><span class="brand-sub">Clinics Australia</span></div>
    </div>
  </section>
</main>
</body>
</html>
```